Project Overview:
We are looking to create a website for a monthly subscription IPTV service in WordPress. The website should provide a seamless user experience for customers to sign up for the service and manage their account information. We need the following pages: Home Page, Product Page, Sign-Up Page, and Account Information Page.

Home Page:
The Home Page design should be simple and clean, with a dark theme and minimalistic design elements. We would like to include graphics of popular movie shows displayed on multiple devices. The page should highlight the key benefits and features of our service and provide a clear call-to-action for visitors to sign up.

Product Page:
The Product Page should provide detailed information about our subscription tiers and pricing plans. It should highlight the key features of each plan and provide a clear comparison between them. The page should also include a call-to-action button for visitors to sign up.

Sign-Up Page:
The Sign-Up Page is the conversion page where members will sign up for the service. It should collect the following information: Name, Phone Number, Email, Password, and Payment Information. The design should be simple, intuitive, and easy to use. It should highlight the benefits of our service and provide a clear call-to-action for visitors to sign up.

Account Information Page:
The Account Information Page should allow members to view and manage their account details. It should include the following information: Profile Image, Contact Details, Password Management, Payment Information Management, and Membership Expiration Date. The design should be user-friendly, intuitive, and easy to navigate.

Goals: The primary goal of the website is to provide an easy-to-use portal for customers to sign up for the service and manage their account information. The website should be user-friendly and visually appealing to attract potential customers.

Scope: The scope of the project includes designing a home page, a sign-up page, an account information page, and a payment information page. The website should be designed to be responsive and accessible on desktop and mobile devices.

Design Preferences: The design should be clean, modern, and visually appealing. The use of a color palette that is consistent with the brand identity is recommended. The website should be easy to navigate and provide a clear call-to-action for users to sign up for the service.

FYI: The subscription service I am designing a website for is related to an IPTV service. IPTV stands for Internet Protocol Television, which is a digital television broadcasting protocol that uses the internet to deliver TV programs and videos to viewers. The website will allow customers to sign up for the IPTV service and access their account information such as user name and password, membership tier, name, and payment details. Please let me know if you have any further questions, and I would be happy to provide more details. Thank you!

Dear Designers,

Thank you for your participation in our project. After reviewing the designs received so far, we have decided to update the brief to better reflect our needs and preferences. We apologize for any confusion this may cause, but we believe that these changes will result in better design submissions and a more successful project overall.

The updated brief is as follows:

We are looking to create a website for WordPress.

Also, here is the updated Brief.

Project Title: WordPress Website Design for Monthly Subscription IPTV Service

Project Overview:
We are looking to create a website for a monthly subscription IPTV service. The website should provide a seamless user experience for customers to sign up for the service and manage their account information. We need the following pages: Home Page, Product Page, Sign-Up Page, and Account Information Page.

Home Page:

Product Page:

Sign-Up Page:

Account Information Page:

Design Preferences:
We prefer a dark theme with minimalistic design elements and hits of our logo colors. The website should be easy to use and navigate, with clear calls-to-action and simple, intuitive forms. The design should be optimized for mobile devices and load quickly.

We hope that these updates provide you with a clearer understanding of our requirements and preferences. Please let us know if you have any questions or concerns. We look forward to seeing your revised designs.

Thank you again for your participation.
We will guarantee this project as soon as we see something we like that meets the updated requirements.

The website's target audience is individuals who are interested in subscribing to the monthly service.

4 page

• One item for sale and a client profile section.

```html
<!DOCTYPE html>
<html lang="en">
<head>
<meta charset="UTF-8">
<title>Streamva – Unlimited Movies, TV Shows and More</title>
<link rel="stylesheet" href="https://fonts.googleapis.com/css2?family=Bangers&family=Poppins:wght@400;500;700;800&display=swap">
<style>
:root{
  --red:#ff0000;
  --black:#000000;
  --ink:#0a0a0a;
  --panel:#1c1c1c;
  --icon-box:#0d0d0d;
  --white:#ffffff;
  --muted:#e6e6e6;
  --hero-top:#1d2a44;
  --hero-bottom:#0b0b10;
}
*{box-sizing:border-box;margin:0;padding:0}
html,body{width:1200px;height:4073px;overflow:hidden;background:var(--black)}
body{position:relative;font-family:"Poppins",sans-serif;color:var(--white)}
.heading{font-family:"Bangers",cursive;font-style:italic;letter-spacing:1px;font-weight:400}
.btn{position:absolute;background:var(--red);color:var(--white);border-radius:6px;font-family:"Bangers",cursive;font-style:italic;font-size:17px;letter-spacing:1px;display:flex;align-items:center;justify-content:center}
.abs{position:absolute}

/* Hero */
.hero{position:absolute;left:0;top:0;width:1200px;height:600px;background:linear-gradient(180deg,var(--hero-top) 0%,#1a2236 45%,var(--hero-bottom) 100%)}
.hero-media{position:absolute;inset:0;background:radial-gradient(ellipse at 50% 40%,rgba(120,110,100,.35),rgba(0,0,0,0) 70%)}
.brand{font-family:"Poppins",sans-serif;font-weight:800;font-size:34px;color:var(--white);letter-spacing:1px}
.menu-icon{position:absolute;left:1075px;top:44px;width:22px}
.menu-icon span{display:block;height:4px;background:var(--white);margin-bottom:4px;border-radius:1px}
.hero-title{position:absolute;top:232px;left:0;width:1200px;text-align:center;font-size:40px}
.hero-text{position:absolute;top:292px;left:225px;width:750px;text-align:center;font-size:13.5px;line-height:24px}
.hero-input{position:absolute;left:387px;top:360px;width:314px;height:42px;background:var(--white);border-radius:6px;color:#333;font-size:12px;padding-left:12px;display:flex;align-items:center}

/* About */
.about{position:absolute;left:0;top:600px;width:1200px;height:447px;background:var(--black)}
.monitor-img{position:absolute;left:135px;top:32px;width:440px;height:370px;border-radius:8px;background:linear-gradient(180deg,#d9d9d9 0%,#1a1a1a 6%,#111 70%,#cfcfcf 72%,#9a9a9a 100%)}
.section-title{font-size:30px}
.body-text{font-size:14px;line-height:25px}

/* Features */
.features{position:absolute;left:0;top:1047px;width:1200px;height:1718px;background:var(--ink)}
.circle{position:absolute;width:434px;height:434px;border-radius:50%}
.feature-text{position:absolute;width:450px}

/* FAQ */
.faq{position:absolute;left:0;top:2765px;width:1200px;height:725px;background:var(--black)}
.faq-title{position:absolute;top:80px;left:0;width:1200px;text-align:center;font-size:32px}
.faq-item{position:absolute;left:104px;width:992px;height:63px;background:var(--panel);display:flex;align-items:center}
.faq-item.open{left:101px;width:996px;height:118px;border:2px solid var(--red);background:var(--black);align-items:flex-start;padding-top:10px}
.faq-icon{width:48px;height:48px;margin-left:11px;background:var(--icon-box);display:flex;align-items:center;justify-content:center;flex:none}
.open .faq-icon{background:var(--red)}
.faq-q{margin-left:32px;font-size:21px;font-weight:500;flex:1}
.faq-a{font-size:14px;line-height:24px;margin-top:4px;width:820px}
.chev{margin-right:30px;flex:none}
.open .faq-body{margin-left:32px;flex:1}
.open .faq-q{margin-left:0}

/* CTA */
.cta{position:absolute;left:101px;top:3490px;width:996px;height:230px;background:var(--red)}
.cta-title{position:absolute;top:40px;left:0;width:996px;text-align:center;font-size:24px}
.cta-field{position:absolute;left:198px;top:100px;width:602px;height:57px;border:1.5px solid var(--white);border-radius:6px;font-size:15px;padding-left:14px;display:flex;align-items:center}
.cta-btn{position:absolute;left:486px;top:8px;width:106px;height:40px;background:var(--white);color:var(--red);border-radius:6px;font-family:"Bangers",cursive;font-style:italic;font-size:17px;display:flex;align-items:center;justify-content:center}

/* Footer */
.footer-brand{position:absolute;left:258px;top:3822px;width:290px;text-align:center;font-size:56px;font-weight:800}
.footer-links{position:absolute;top:3822px;list-style:none;font-size:16px;line-height:29.5px}
.copyright{position:absolute;top:3960px;left:0;width:1200px;text-align:center;font-size:10px}
.social{position:absolute;top:4000px;width:27px;height:27px;border-radius:50%;background:var(--red)}
</style>
</head>
<body>

<header class="hero">
  <div class="hero-media" role="img" aria-label="Wall of many TV screens showing movie and show stills"></div>
  <div class="abs brand" style="left:105px;top:30px">STREAMVA</div>
  <div class="btn" style="left:955px;top:38px;width:86px;height:32px;font-size:15px">Sign up</div>
  <div class="menu-icon"><span></span><span></span><span></span></div>
  <h1 class="hero-title heading">Unlimited movies, TV shows and more</h1>
  <p class="hero-text">Lorem ipsum dolor sit amet, consectetur adipiscing elit, sed do eiusmod tempor incididunt ut labore et dolore magna aliqua. Ut enim ad minim veniam, ex ea commodo consequat.</p>
  <div class="hero-input">Enter Email</div>
  <div class="btn" style="left:708px;top:360px;width:106px;height:42px">Submit</div>
</header>

<section class="about">
  <div class="monitor-img" role="img" aria-label="Desktop monitor showing the Streamva brand on screen"></div>
  <h2 class="abs heading section-title" style="left:641px;top:32px">About Streamva</h2>
  <div class="abs" style="left:641px;top:80px;width:456px">
    <p class="body-text" style="text-align:justify">Lorem ipsum dolor sit amet, consectetur adipiscing elit, sed do eiusmod tempor incididunt ut labore et dolore magna aliqua. Ut enim ad veniam, exercitation ullamco laboris nisi ut aliquip ex ea commodo consequat. Duis aute irure dolor in reprehenderit in voluptate velit esse cillum dolore eu fugiat nulla pariatur.</p>
    <p class="body-text" style="text-align:justify;margin-top:6px">Sed ut perspiciatis unde omnis iste natus error sit voluptatem accusantium laudantium, totam rem aperiam, eaque ipsa quae ab illo inventore veritatis et quasi architecto beatae vitae dicta sunt explicabo.</p>
  </div>
  <div class="btn" style="left:641px;top:325px;width:107px;height:40px">Read more</div>
</section>

<section class="features">
  <div class="feature-text" style="left:104px;top:272px">
    <h2 class="heading section-title">Enjoy on your TV.</h2>
    <p class="body-text" style="margin-top:14px">Sed ut perspiciatis unde omnis iste natus error sit voluptatem accusantium doloremque laudantium, totam rem aperiam, eaque ipsa quae ab illo inventore veritatis et quasi architecto beatae vitae dicta sunt explicabo.</p>
  </div>
  <div class="btn" style="left:104px;top:449px;width:107px;height:42px">Read more</div>
  <div class="circle" style="left:656px;top:178px;background:radial-gradient(circle at 45% 45%,#3a5f8f,#1f3a5e 60%,#16283f)" role="img" aria-label="Hand holding a remote in front of a TV streaming menu"></div>

  <div class="circle" style="left:116px;top:632px;background:radial-gradient(circle at 50% 45%,#3f7be0,#8ba2bf 55%,#6a7f98)" role="img" aria-label="Hand holding a phone showing a download screen"></div>
  <div class="feature-text" style="left:640px;top:732px">
    <h2 class="heading section-title" style="line-height:38px">Download your shows to watch offline.</h2>
    <p class="body-text" style="margin-top:14px">Sed ut perspiciatis unde omnis iste natus error sit voluptatem accusantium doloremque laudantium, totam rem aperiam, eaque ipsa quae ab illo inventore veritatis et quasi architecto beatae vitae dicta sunt explicabo.</p>
  </div>
  <div class="btn" style="left:645px;top:938px;width:107px;height:42px">Read more</div>

  <div class="feature-text" style="left:104px;top:1233px">
    <h2 class="heading section-title">Create profiles for children.</h2>
    <p class="body-text" style="margin-top:14px">Sed ut perspiciatis unde omnis iste natus error sit voluptatem accusantium doloremque laudantium, totam rem aperiam, eaque ipsa quae ab illo inventore veritatis et quasi architecto beatae vitae dicta sunt explicabo.</p>
  </div>
  <div class="btn" style="left:104px;top:1405px;width:107px;height:42px">Read more</div>
  <div class="circle" style="left:656px;top:1128px;background:radial-gradient(circle at 50% 50%,#6b5040,#a88a70 50%,#cfc4b6)" role="img" aria-label="Child watching cartoons on a living room TV"></div>
</section>

<section class="faq">
  <h2 class="faq-title heading">Frequently asked questions</h2>
  <div class="faq-item open" style="top:165px">
    <div class="faq-icon"><svg width="22" height="22" viewBox="0 0 22 22"><circle cx="11" cy="11" r="10" fill="#fff"/><rect x="9.5" y="9" width="3" height="8" fill="#ff0000"/><circle cx="11" cy="6" r="1.7" fill="#ff0000"/></svg></div>
    <div class="faq-body">
      <div class="faq-q">Lorem ipsum dolor sit amet</div>
      <p class="faq-a">Stablr is a social media management platform designed specifically for horse owners and riders. It allows you to organize and share content related to your horses on various social media networks with ease.</p>
    </div>
    <svg class="chev" style="margin-top:14px" width="18" height="18" viewBox="0 0 18 18"><circle cx="9" cy="9" r="8" fill="none" stroke="#ff0000" stroke-width="2"/><path d="M5.5 10.5 9 7l3.5 3.5" fill="none" stroke="#ff0000" stroke-width="2"/></svg>
  </div>
  <div class="faq-item" style="top:290px"><div class="faq-icon"><svg width="22" height="22" viewBox="0 0 22 22"><circle cx="11" cy="11" r="10" fill="#fff"/><rect x="9.5" y="9" width="3" height="8" fill="#0d0d0d"/><circle cx="11" cy="6" r="1.7" fill="#0d0d0d"/></svg></div><div class="faq-q">consectetur adipiscing elit, sed do eiusmod</div><svg class="chev" width="18" height="18" viewBox="0 0 18 18"><circle cx="9" cy="9" r="8" fill="#fff"/><path d="M5.5 7.5 9 11l3.5-3.5" fill="none" stroke="#1c1c1c" stroke-width="2"/></svg></div>
  <div class="faq-item" style="top:365px"><div class="faq-icon"><svg width="22" height="22" viewBox="0 0 22 22"><circle cx="11" cy="11" r="10" fill="#fff"/><rect x="9.5" y="9" width="3" height="8" fill="#0d0d0d"/><circle cx="11" cy="6" r="1.7" fill="#0d0d0d"/></svg></div><div class="faq-q">sed do eiusmod</div><svg class="chev" width="18" height="18" viewBox="0 0 18 18"><circle cx="9" cy="9" r="8" fill="#fff"/><path d="M5.5 7.5 9 11l3.5-3.5" fill="none" stroke="#1c1c1c" stroke-width="2"/></svg></div>
  <div class="faq-item" style="top:437px"><div class="faq-icon"><svg width="22" height="22" viewBox="0 0 22 22"><circle cx="11" cy="11" r="10" fill="#fff"/><rect x="9.5" y="9" width="3" height="8" fill="#0d0d0d"/><circle cx="11" cy="6" r="1.7" fill="#0d0d0d"/></svg></div><div class="faq-q">Lorem ipsum dolor sit amet</div><svg class="chev" width="18" height="18" viewBox="0 0 18 18"><circle cx="9" cy="9" r="8" fill="#fff"/><path d="M5.5 7.5 9 11l3.5-3.5" fill="none" stroke="#1c1c1c" stroke-width="2"/></svg></div>
  <div class="faq-item" style="top:509px"><div class="faq-icon"><svg width="22" height="22" viewBox="0 0 22 22"><circle cx="11" cy="11" r="10" fill="#fff"/><rect x="9.5" y="9" width="3" height="8" fill="#0d0d0d"/><circle cx="11" cy="6" r="1.7" fill="#0d0d0d"/></svg></div><div class="faq-q">Dolor sit amet Lorem ipsum</div><svg class="chev" width="18" height="18" viewBox="0 0 18 18"><circle cx="9" cy="9" r="8" fill="#fff"/><path d="M5.5 7.5 9 11l3.5-3.5" fill="none" stroke="#1c1c1c" stroke-width="2"/></svg></div>
  <div class="faq-item" style="top:581px"><div class="faq-icon"><svg width="22" height="22" viewBox="0 0 22 22"><circle cx="11" cy="11" r="10" fill="#fff"/><rect x="9.5" y="9" width="3" height="8" fill="#0d0d0d"/><circle cx="11" cy="6" r="1.7" fill="#0d0d0d"/></svg></div><div class="faq-q">Ipsum dolor sit amet</div><svg class="chev" width="18" height="18" viewBox="0 0 18 18"><circle cx="9" cy="9" r="8" fill="#fff"/><path d="M5.5 7.5 9 11l3.5-3.5" fill="none" stroke="#1c1c1c" stroke-width="2"/></svg></div>
</section>

<section class="cta">
  <h2 class="cta-title heading">Ready to watch? Enter your email to create or restart your membership.</h2>
  <div class="cta-field">Enter Email<div class="cta-btn">Submit</div></div>
</section>

<footer>
  <div class="footer-brand">STREAMVA</div>
  <ul class="footer-links" style="left:638px"><li>FAQ</li><li>Help Centre</li><li>Account</li><li>Contact Us</li></ul>
  <ul class="footer-links" style="left:792px"><li>Terms of Use</li><li>Privacy</li><li>Cookie Preferences</li><li>&nbsp;Information</li></ul>
  <p class="copyright heading">Copyright © 2023 Streamva | All rights reserved</p>
  <div class="social" style="left:545px"></div>
  <div class="social" style="left:586px"></div>
  <div class="social" style="left:627px"></div>
</footer>

</body>
</html>
```